New Innovative Counselling and psychotherapy Service needs Business Card design

Keep it simple and professional. On one side, just company name and logo (perhaps in all blue) and maybe a tag line.

On other side (all white) my name and Qualifications in centre

Industry/Entity Type

Health And Wellness

Contact Information for Business Card

Dara Whelby
Counsellor & Psychotherapist
BSc (Psychol.), BA, Dip. (Couns. & Psych.), PG.Cert (CBT), FGTrK, ONRE

I will also require Mobile no, Email and web site address of which I'll pass on to final designer.

Font styles to use
Sans Serif

Requirements
Must have
• My Logo Only and please use the colours in logo that is in it.
Should not have
• Any other images

```html
<!DOCTYPE html>
<html lang="en">
<head>
<meta charset="utf-8">
<title>Kindred Lane – Business Card</title>
<link href="https://fonts.googleapis.com/css2?family=Montserrat:wght@300&family=Open+Sans:wght@400;600&family=Cormorant+Garamond:ital@1&display=swap" rel="stylesheet">
<style>
  :root{
    --stage:#cfd1d3;
    --card-light:#efefef;
    --card-dark:#3b3b3b;
    --ink:#3a3a3a;
    --ink-soft:#d9d9d9;
    --brand-blue:#41b1ea;
    --brand-green:#94d35b;
  }
  *{box-sizing:border-box;margin:0;padding:0}
  html,body{width:1200px;height:896px;overflow:hidden}
  body{
    background:var(--stage);
    font-family:"Open Sans",Arial,sans-serif;
    display:flex;flex-direction:column;align-items:center;justify-content:center;gap:56px;
  }
  .card{
    width:630px;height:360px;position:relative;
    box-shadow:0 6px 18px rgba(0,0,0,.18);
    overflow:hidden;
  }
  .card--front{background:var(--card-light);color:var(--ink)}
  .card--back{background:var(--card-dark);color:var(--ink-soft)}

  .wordmark{
    font-family:"Montserrat",Arial,sans-serif;font-weight:300;
    letter-spacing:.5px;white-space:nowrap;
  }
  .card--front .wordmark{
    position:absolute;left:250px;top:52px;font-size:44px;color:var(--ink);
  }
  .front-accent{
    position:absolute;left:-70px;top:-40px;width:300px;height:300px;border-radius:50%;
    background:var(--brand-blue);
  }
  .details{position:absolute;left:250px;top:140px;font-size:14px;line-height:1.45}
  .details .name{
    font-family:"Montserrat",Arial,sans-serif;font-size:18px;text-transform:uppercase;
    color:var(--brand-blue);letter-spacing:.5px;margin-bottom:2px;
  }
  .details .name .surname{color:var(--brand-green)}
  .details .role{margin-bottom:0}
  .contact{list-style:none;margin-top:10px}
  .contact li{display:flex;align-items:center;gap:8px}
  .contact svg{width:12px;height:12px;flex:none;fill:var(--brand-blue)}

  .brand-lockup{
    position:absolute;left:70px;top:120px;display:flex;align-items:center;gap:16px;
  }
  .brand-dot{width:40px;height:40px;border-radius:50%;background:var(--brand-blue)}
  .card--back .wordmark{font-size:38px;color:var(--ink-soft)}
  .tagline{
    position:absolute;left:70px;top:190px;
    font-family:"Cormorant Garamond",Georgia,serif;font-style:italic;
    font-size:24px;line-height:1.25;color:var(--ink-soft);
  }
</style>
</head>
<body>

  <section class="card card--front" aria-label="Business card front">
    <div class="front-accent"></div>
    <div class="wordmark">Kindred Lane</div>
    <div class="details">
      <p class="name">Dara <span class="surname">Whelby</span></p>
      <p class="role">Counsellor &amp; Psychotherapist</p>
      <p class="quals">BSc (Psychol.), BA, Dip. (Couns. &amp; Psych.),</p>
      <p class="quals">PG.Cert (CBT), FGTrK, ONRE</p>
      <ul class="contact">
        <li><svg viewBox="0 0 12 12" aria-hidden="true"><path d="M2 1h3l1 3-1.5 1a7 7 0 0 0 2.5 2.5L8 6l3 1v3a1 1 0 0 1-1 1A9 9 0 0 1 1 2a1 1 0 0 1 1-1z"/></svg>087 5520 419</li>
        <li><svg viewBox="0 0 12 12" aria-hidden="true"><path d="M1 2.5h10v7H1z M1 2.5l5 4 5-4" stroke="#efefef" stroke-width=".8"/></svg>info@kindredlane.com</li>
        <li><svg viewBox="0 0 12 12" aria-hidden="true"><circle cx="6" cy="6" r="5"/></svg>www.kindredlane.com</li>
      </ul>
    </div>
  </section>

  <section class="card card--back" aria-label="Business card back">
    <div class="brand-lockup">
      <span class="brand-dot"></span>
      <span class="wordmark">Kindred Lane</span>
    </div>
    <p class="tagline">Caring For Your Psychological<br>Well-Being Is Our Top Priority</p>
  </section>

</body>
</html>
```